Business Card for a Jewellery Brand

Business card for an upscale jewellery brand. Attached is the brand logo and icon and color board. I am looking for two card versions: one for the founder and one is generic. The card should be elegant and convey upscale and premium feel. I am open to both square and rectangle card shapes.

Industry/Entity Type

Jewelry

Contact Information for Business Card

Two cards: (1) Sunela Parvaniya (Founder) (2) General
(1) Sunela Parvaniya card should have Name: Sunela Parvaniya, Title: Founder Email id: sunela@quiremo.com.au. Phone no: +61452913307
(2) Generic card should have Email id: info@quiremo.com.au. Phone no: +61436207518

Requirements
Must have
• Workmark
• ICON
• Phone no
• Email ID
• ABN: 58219740312 (Note: ABN is Business number in Australia)
• Website: www.quiremo.com.au
• Instagram: quiremo_jewellery
• Facebook: @quiremojewellery
Nice to have
• Tagline

```html
<!DOCTYPE html>
<html lang="en">
<head>
<meta charset="utf-8">
<title>Quiremo Business Cards</title>
<link rel="stylesheet" href="https://fonts.googleapis.com/css2?family=Roboto:wght@300;400;500&family=Roboto+Condensed:wght@500&display=swap">
<style>
  :root {
    --blush: #dc8e8b;
    --blush-soft: #e29d9a;
    --paper: #f3f3f3;
    --backdrop: #e2e2e2;
    --ink: #3f3f3f;
    --ink-muted: #6b6b6b;
    --white: #ffffff;
  }
  * { margin: 0; padding: 0; box-sizing: border-box; }
  html, body {
    width: 1200px;
    height: 960px;
    overflow: hidden;
    background: var(--backdrop);
    font-family: "Roboto", Arial, sans-serif;
  }
  .card {
    position: absolute;
    width: 600px;
    overflow: hidden;
  }
  .card--front {
    left: 302px;
    top: 130px;
    height: 335px;
    background: var(--paper);
  }
  .card--back {
    left: 300px;
    top: 488px;
    height: 342px;
    background: var(--blush);
  }
  .front-band {
    position: absolute;
    left: 0; top: 0;
    width: 100%;
    height: 82px;
    background: var(--blush);
  }
  .brand-mark {
    position: absolute;
    left: 258px;
    top: 30px;
    width: 84px;
    height: 84px;
    border-radius: 50%;
    background: var(--paper);
    border: 2px solid var(--blush);
  }
  .wordmark {
    position: absolute;
    left: 0;
    width: 100%;
    text-align: center;
    font-weight: 500;
    white-space: nowrap;
    line-height: 1;
  }
  .card--front .wordmark {
    top: 129px;
    font-size: 42px;
    letter-spacing: 6px;
    padding-left: 6px;
    color: var(--blush);
  }
  .holder-name {
    position: absolute;
    top: 211px;
    width: 100%;
    text-align: center;
    font-family: "Roboto Condensed", "Arial Narrow", sans-serif;
    font-weight: 500;
    font-size: 20px;
    color: var(--blush);
  }
  .holder-title {
    position: absolute;
    top: 237px;
    width: 100%;
    text-align: center;
    font-size: 14px;
    font-weight: 500;
    color: var(--ink-muted);
  }
  .contact-line {
    position: absolute;
    width: 100%;
    display: flex;
    justify-content: center;
    align-items: center;
    gap: 3px;
    font-size: 13.5px;
    color: var(--ink);
    white-space: nowrap;
  }
  .contact-line--primary { top: 266px; }
  .contact-line--secondary { top: 286px; }
  .contact-item { display: inline-flex; align-items: center; gap: 3px; }
  .contact-icon { width: 11px; height: 11px; flex: none; }
  .social-mark {
    width: 9px; height: 9px;
    background: var(--blush);
    border-radius: 1px;
    flex: none;
  }
  .back-pattern {
    position: absolute;
    inset: 0;
    background: linear-gradient(160deg, var(--blush-soft), var(--blush));
  }
  .card--back .wordmark {
    top: 120px;
    font-size: 78px;
    letter-spacing: 12px;
    padding-left: 12px;
    color: var(--white);
  }
  .tagline {
    position: absolute;
    top: 207px;
    left: 0;
    width: 100%;
    display: flex;
    justify-content: center;
    align-items: center;
    gap: 4px;
    font-size: 13px;
    color: var(--white);
  }
  .tagline-rule {
    width: 95px;
    height: 1px;
    background: linear-gradient(90deg, rgba(255,255,255,0), var(--white));
  }
  .tagline-rule--right {
    background: linear-gradient(90deg, var(--white), rgba(255,255,255,0));
  }
</style>
</head>
<body>

<section class="card card--front" aria-label="Founder card front">
  <div class="front-band"></div>
  <div class="brand-mark" aria-hidden="true"></div>
  <div class="wordmark">QUIREMO</div>
  <div class="holder-name">Sunela Parvaniya</div>
  <div class="holder-title">Founder</div>

  <div class="contact-line contact-line--primary">
    <span class="contact-item">
      <svg class="contact-icon" viewBox="0 0 12 12" aria-hidden="true">
        <rect x="3" y="0.5" width="6" height="11" rx="1" fill="none" stroke="var(--blush)" stroke-width="1.2"/>
        <line x1="5" y1="9.5" x2="7" y2="9.5" stroke="var(--blush)" stroke-width="1"/>
      </svg>+61452913307
    </span>
    <span class="contact-item">
      <svg class="contact-icon" viewBox="0 0 12 12" aria-hidden="true">
        <rect x="0.5" y="2.5" width="11" height="7" fill="var(--blush)"/>
        <polyline points="0.5,2.5 6,6.5 11.5,2.5" fill="none" stroke="var(--white)" stroke-width="1"/>
      </svg>sunela@quiremo.com.au
    </span>
    <span class="contact-item"><span class="social-mark"></span>quiremo_jewellery</span>
    <span class="contact-item"><span class="social-mark"></span>@quiremojewellery</span>
  </div>

  <div class="contact-line contact-line--secondary">
    <span class="contact-item">
      <svg class="contact-icon" viewBox="0 0 12 12" aria-hidden="true">
        <circle cx="6" cy="6" r="5.3" fill="var(--blush)"/>
        <ellipse cx="6" cy="6" rx="2.2" ry="5.3" fill="none" stroke="var(--white)" stroke-width="0.8"/>
        <line x1="0.7" y1="6" x2="11.3" y2="6" stroke="var(--white)" stroke-width="0.8"/>
      </svg>www.quiremo.com.au | ABN: 58219740312
    </span>
  </div>
</section>

<section class="card card--back" aria-label="Card back">
  <div class="back-pattern" role="img" aria-label="Repeating faint geometric brand pattern in soft blush tones"></div>
  <div class="wordmark">QUIREMO</div>
  <div class="tagline">
    <span class="tagline-rule"></span>
    <span>LOVE IS IN THE AIR</span>
    <span class="tagline-rule tagline-rule--right"></span>
  </div>
</section>

</body>
</html>
```